Velvet Dice Night Age Verification Landing Page

To create a visually appealing design for the landing page of the adult game "Velvet Dice Night" that confirms the visitor's age.
The design should have a simple and visually appealing look that focuses on two buttons labeled "Yes" and "No". The purpose of the page is to confirm that the visitor is 18 years of age or older before accessing the game's content. Responsive design that works well on desktop and mobile devices. The final output should be delivered in PSD, AI, or Sketch format, along with any necessary images or assets.
I have also attached examples.

```html
<!DOCTYPE html>
<html lang="en">
<head>
<meta charset="utf-8">
<title>Velvet Dice Night – Age Verification</title>
<link rel="stylesheet" href="https://fonts.googleapis.com/css2?family=Lato:wght@400;700&display=swap">
<style>
  :root {
    --bg-red: #8a1a3a;
    --bg-rose: #a33a5e;
    --bg-plum: #96609e;
    --bg-deep: #7e1633;
    --modal: rgba(70, 8, 20, 0.86);
    --accent: #b80316;
    --accent-border: #c0101f;
    --text: #ffffff;
  }
  * { margin: 0; padding: 0; box-sizing: border-box; }
  html, body {
    width: 1200px;
    height: 819px;
    overflow: hidden;
  }
  body {
    position: relative;
    font-family: "Lato", sans-serif;
    color: var(--text);
    background: var(--bg-red);
  }
  .hero-photo {
    position: absolute;
    inset: 0;
    background:
      radial-gradient(ellipse 40% 45% at 62% 45%, rgba(210, 140, 150, 0.35), transparent 70%),
      linear-gradient(115deg, var(--bg-red) 0%, var(--bg-rose) 45%, var(--bg-plum) 80%, var(--bg-deep) 100%);
  }
  .age-gate {
    position: absolute;
    left: 297px;
    top: 183px;
    width: 607px;
    height: 455px;
    background: var(--modal);
    display: flex;
    flex-direction: column;
    align-items: center;
  }
  .brand {
    margin-top: 112px;
    display: flex;
    align-items: center;
    gap: 10px;
    font-weight: 700;
    font-size: 26px;
    letter-spacing: 0.5px;
  }
  .brand-dot {
    width: 14px;
    height: 14px;
    border-radius: 50%;
    background: var(--text);
  }
  .age-question {
    margin-top: 64px;
    font-size: 21px;
    font-weight: 400;
    letter-spacing: -0.2px;
  }
  .answer-row {
    margin-top: 25px;
    display: flex;
    gap: 32px;
  }
  .answer {
    height: 52px;
    display: flex;
    align-items: center;
    justify-content: center;
    font-size: 23px;
    font-weight: 700;
    color: var(--text);
    text-decoration: none;
  }
  .answer-yes { width: 154px; background: var(--accent); }
  .answer-no { width: 158px; border: 2px solid var(--accent-border); background: transparent; }
  .remember {
    margin-top: 22px;
    display: flex;
    align-items: center;
    gap: 12px;
    font-size: 11.5px;
    font-weight: 700;
  }
  .remember-box {
    width: 10px;
    height: 10px;
    border-radius: 2px;
    background: var(--text);
  }
</style>
</head>
<body>
  <div class="hero-photo" role="img" aria-label="Tinted photograph of a couple embracing on a bed"></div>

  <section class="age-gate">
    <div class="brand">
      <span class="brand-dot"></span>
      <span class="brand-name">Velvet Dice Night</span>
    </div>
    <p class="age-question">Are you over 18 years of age?</p>
    <div class="answer-row">
      <a class="answer answer-yes" href="#">Yes</a>
      <a class="answer answer-no" href="#">No</a>
    </div>
    <label class="remember">
      <span class="remember-box"></span>
      <span>Remember Me</span>
    </label>
  </section>
</body>
</html>
```